Redesign 2016 Digital Marketing Website and Convert to Wordpress

Technology needed to integrate:

- redesign and convert to wordpress
- gravity forms
- malware and hacker defense / honeypot (must be very secure from hackers)
- I want gravity forms to be a flow that asks many questions with icons and progress bar.
- 1 home page design
- 1 blog design
- 1 design for internal page content
- 1 multi step gravity form
I want to focus on SMB's. We are a marketing agency thats been around since 2016.

Site is: tallpine.agency

I am looking to redesign the homepage, blog page and services page. The services page will be a template for all inner pages of the site. All content needs to be moved into the new design.

I want to get ride of the weird video.

I need you to install gravity forms pro model so we can pass utms.

I need the gravity form to be a multi step form with icons.

All "contact us" or "get a free assesments" call to actions will go to this form only.

step 1:
what is your website

step 2:
what industry are you in
- option
- Home Services
- Legal
- Ecommerce
- Lead Gen

No matter which one they select its going to produce a differnt calculator for them.

Law:
How many leads did you get last month
how much is each ase worth on average
How much revenue do you want to make

Home servicse:
How many bookings did you get last month
How much is each service worht on average
How much revenue do you wangt to make

Ecommerce:
What is your average order value
How muny purchases did you have last month
How much revenue did you drive
How much revenue do you want to drive

For lead gen:
How many leads did you get lawt month
How much revenue did they generate

Step 3:
What is your current advertising budget

step 4:
Do you have a CRM and if so what is it

Step 5:
What is your personal informagtion
name
email
phone

Let me know if this is enough to get you going

Small and medium sized law firms, ecommerce, home services and lead gen customers.

We are a digital marketing agency

• Use whats on the current site and improve upon it

• Must be very secure, developed into a wordpress website. using gravity forms. remove my photo and my staffs photo, depersonalize it so it doesnt mention me or sam crolley. Use the same color scheme. I am looking to redesign the homepage, blog page and services page. The services page will be a template for all inner pages of the site. All content needs to be moved into the new design. I want to get ride of the weird video. I need you to install gravity forms pro model so we can pass utms. I need the gravity form to be a multi step form with icons. All "contact us" or "get a free assesments" call to actions will go to this form only. step 1: what is your website step 2: what industry are you in - option - Home Services - Legal - Ecommerce - Lead Gen No matter which one they select its going to produce a differnt calculator for them. Law: How many leads did you get last month how much is each ase worth on average How much revenue do you want to make Home servicse: How many bookings did you get last month How much is each service worht on average How much revenue do you wangt to make Ecommerce: What is your average order value How muny purchases did you have last month How much revenue did you drive How much revenue do you want to drive For lead gen: How many leads did you get lawt month How much revenue did they generate How much revenue do you want to make Step 3: What is your current advertising budget step 4: Do you have a CRM and if so what is it Step 5: What is your personal informagtion name email phone Let me know if this is enough to get you going
• SHOULD NOT BE SLOPPY, I AM LOOKING FOR ATTENTION TO DETAIL.

```html
<!DOCTYPE html>
<html lang="en">
<head>
<meta charset="utf-8">
<title>Legal Marketing | Tall Pine</title>
<link rel="stylesheet" href="https://fonts.googleapis.com/css2?family=Montserrat:wght@400;500;600;700&display=swap">
<style>
:root{
  --red:#7d1414;
  --red-deep:#5e0b0b;
  --red-bright:#9c1b1b;
  --ink:#1c1c1c;
  --text:#333;
  --muted:#555;
  --gray:#e6e6e6;
  --line:#d5d5d5;
  --white:#fff;
  --accent:#d9553b;
}
*{box-sizing:border-box;margin:0;padding:0}
html,body{width:1200px;height:5391px;overflow:hidden}
body{font-family:"Montserrat",sans-serif;color:var(--text);background:var(--white);position:relative}
.abs{position:absolute}
a{color:inherit;text-decoration:none}

/* header */
.site-header{position:absolute;top:0;left:0;width:1200px;height:65px;background:var(--white);box-shadow:0 1px 4px rgba(0,0,0,.12);z-index:2}
.brand{position:absolute;display:flex;align-items:center;gap:10px}
.brand-dot{width:50px;height:50px;border-radius:50%;background:var(--red)}
.brand-name{font-size:22px;font-weight:500;letter-spacing:2px;color:var(--ink)}
.header-brand{left:98px;top:7px}
.main-nav{position:absolute;left:382px;top:23px;display:flex;gap:44px;font-size:13px;font-weight:600;color:var(--ink)}
.main-nav .active{border-bottom:2px solid var(--red);padding-bottom:6px}
.header-cta{position:absolute;right:0;top:0;width:236px;height:65px;background:var(--red);clip-path:polygon(22px 0,100% 0,100% 100%,0 100%);color:var(--white);padding:14px 0 0 44px}
.header-cta strong{display:block;font-size:12px;font-weight:700}
.header-cta span{display:block;font-size:10px;margin-top:3px}

/* hero */
.hero{position:absolute;top:65px;left:0;width:1200px;height:421px;background:radial-gradient(ellipse at 60% 70%,#3a3a3a 0%,#1e1e1e 55%,#141414 100%);text-align:center;color:var(--white)}
.hero-kicker{position:absolute;top:142px;width:100%;font-size:24px;font-weight:400;letter-spacing:1px}
.hero-title{position:absolute;top:172px;width:100%;font-size:42px;font-weight:500;letter-spacing:1px}

/* intro */
.section-title{font-size:32px;font-weight:600;line-height:1.15;color:var(--ink);text-transform:uppercase}
.section-title em{font-style:normal;color:var(--red)}
.title-rule{width:110px;height:2px;background:var(--line);margin-top:14px}
.intro-copy{left:117px;top:600px;width:520px}
.intro-copy h3{font-size:19px;font-weight:600;color:var(--ink);line-height:1.35;margin-top:34px}
.intro-copy p{font-size:13.5px;line-height:1.45;margin-top:12px}
.intro-photo-back{left:662px;top:605px;width:234px;height:150px;background:var(--red);border-radius:14px}
.intro-photo{left:678px;top:624px;width:397px;height:356px;border-radius:14px;background:linear-gradient(135deg,#c9cfd6,#8e98a4 60%,#6d6258)}
.intro-wide{left:119px;top:1042px;width:900px;font-size:13.5px;line-height:1.7}
.badges{left:140px;top:1225px;width:880px;display:flex;justify-content:space-between;align-items:center}
.badge-wide{width:200px;height:90px;border-radius:8px;background:#eef0f2}
.badge-hex{width:104px;height:112px;background:#e8edf6;clip-path:polygon(50% 0,100% 25%,100% 75%,50% 100%,0 75%,0 25%);border:0}
.badge-wide.alt{width:170px}

/* why + services */
.why-band{position:absolute;top:1380px;left:0;width:1200px;height:1133px;background:linear-gradient(var(--white) 0 484px,var(--gray) 484px)}
.why-box{left:96px;top:40px;width:998px;height:538px;border-radius:6px;background:linear-gradient(170deg,var(--red-bright),var(--red-deep));color:var(--white);text-align:center;padding:62px 70px 0}
.why-box h2{font-size:22px;font-weight:600;line-height:1.6;text-transform:uppercase}
.why-box p{font-size:13px;line-height:1.6;margin-top:14px}
.why-box p.first{margin-top:48px}
.dashboard{left:105px;top:655px;width:481px;height:384px;background:linear-gradient(160deg,#f7f9fa,#dde6ea);border-radius:4px}
.services-copy{left:622px;top:698px;width:480px}
.services-copy .section-title{font-size:29px}
.services-copy p{font-size:13.5px;line-height:1.5;margin-top:44px}
.btn{display:inline-block;border-radius:26px;font-size:13px;font-weight:700;color:var(--white);text-align:center}
.btn-red{background:var(--red)}
.services-btn{left:618px;top:965px;width:180px;height:48px;line-height:48px}

/* differences */
.different{position:absolute;top:2513px;left:0;width:1200px;height:911px;background:var(--white)}
.center-title{position:absolute;width:100%;text-align:center;font-size:31px;font-weight:600;color:var(--ink);text-transform:uppercase}
.center-title em{font-style:normal;color:var(--red)}
.different .center-title{top:64px}
.different-lead{left:170px;width:860px;text-align:center;font-size:13.5px;line-height:1.55}
.card{width:289px;height:257px;border:2px solid var(--red);text-align:center;padding:22px 24px 0}
.card svg{width:54px;height:54px}
.card h4{font-size:13px;font-weight:700;color:var(--ink);line-height:1.45;margin-top:14px;text-transform:uppercase}
.card p{font-size:13px;line-height:1.45;margin-top:8px;color:var(--muted)}

/* testimonials */
.testimonials{position:absolute;top:3424px;left:0;width:1200px;height:576px;background:var(--gray)}
.testimonials .center-title{top:70px;line-height:1.2;font-size:30px}
.quote-card{left:243px;top:174px;width:689px;height:301px;background:var(--white);border:1px solid var(--line)}
.quote-photo{left:40px;top:35px;width:192px;height:203px;background:linear-gradient(160deg,#e8e3dc,#cdbfae)}
.quote-text{left:268px;top:65px;width:390px;font-size:14px;line-height:1.45}
.quote-name{left:268px;top:214px;font-size:19px;font-weight:500;letter-spacing:2px;color:var(--accent)}
.quote-mark{left:584px;top:225px}
.arrow{top:300px}

/* featured */
.featured{position:absolute;top:4000px;left:0;width:1200px;height:261px;background:var(--white)}
.featured h5{position:absolute;top:44px;width:100%;text-align:center;font-size:20px;font-weight:500;letter-spacing:1px;color:var(--ink)}
.press{top:104px;width:160px;height:80px;background:var(--white);box-shadow:0 2px 8px rgba(0,0,0,.12);display:flex;align-items:center;justify-content:center}
.press i{display:block;width:110px;height:22px;border-radius:4px;background:#d9dde3}

/* office */
.office{position:absolute;top:4261px;left:0;width:1200px;height:555px;background:linear-gradient(170deg,var(--red-bright),var(--red-deep));color:var(--white)}
.office h2{position:absolute;left:155px;top:108px;font-size:30px;font-weight:600;text-transform:uppercase}
.contact-item{left:150px;display:flex;align-items:center;gap:18px;font-size:15px;font-weight:500;line-height:1.6}
.contact-icon{width:42px;height:42px;border-radius:50%;background:var(--white);display:flex;align-items:center;justify-content:center;flex:none}
.office-photo{left:634px;top:240px;width:304px;height:304px;border-radius:50%;background:linear-gradient(160deg,#d7dbe2,#8fa0b6 60%,#7a5e4c);border:4px solid rgba(255,255,255,.5)}

/* footer */
.site-footer{position:absolute;top:4816px;left:0;width:1200px;height:575px;background:var(--white)}
.footer-brand{left:136px;top:32px}
.btn-gray{background:#a9a9a9}
.footer-call{left:607px;top:36px;width:214px;height:48px;line-height:48px}
.footer-grow{left:838px;top:36px;width:215px;height:48px;line-height:48px}
.footer-rule{left:136px;top:110px;width:928px;height:1px;background:var(--line)}
.footer-col{top:148px}
.footer-col h6{font-size:14px;font-weight:700;color:var(--ink);border-left:3px solid var(--red);padding-left:9px;text-transform:uppercase}
.footer-col ul{list-style:none;margin-top:12px;padding-left:16px}
.footer-col li{font-size:12px;line-height:23px;color:var(--muted)}
.copyright-rule{left:0;top:503px;width:1200px;height:1px;background:var(--line)}
.copyright{top:528px;width:100%;text-align:center;font-size:11px;color:var(--muted)}
</style>
</head>
<body>

<header class="site-header">
  <div class="brand header-brand"><span class="brand-dot"></span><span class="brand-name">TALL PINE</span></div>
  <nav class="main-nav">
    <a href="#">ABOUT</a><a href="#" class="active">INDUSTRIES</a><a href="#">SERVICES</a><a href="#">BLOG</a><a href="#">CONTACT US</a>
  </nav>
  <a href="#" class="header-cta"><strong>GET A FREE CONSULTATION</strong><span>OR CALL US (480) 555-0142</span></a>
</header>

<section class="hero">
  <p class="hero-kicker">INDUSTRIES</p>
  <h1 class="hero-title">LEGAL MARKETING</h1>
</section>

<section>
  <div class="abs intro-copy">
    <h2 class="section-title">Legal Marketing for<br><em>Attorneys &amp; Law Firms</em></h2>
    <div class="title-rule"></div>
    <h3>Award-Winning Online Marketing for Attorneys, Law Firms, &amp; Legal Services</h3>
    <p>If you want to acquire more clients and cases, optimize marketing costs, and become THE legal authority in your market, there’s only one solution: digital marketing services from an award-winning legal marketing agency.</p>
    <p>Running a successful law office or working as an independent attorney requires hard work, a dedication to representing your clients and understanding the law. If you are looking for ways to attract and acquire more clients, using professional legal digital marketing services is a must. With the right digital marketing strategy, you can optimize your marketing budget as you maximize your online reach, visibility, and overall ability to grow your clientele.</p>
  </div>
  <div class="abs intro-photo-back"></div>
  <div class="abs intro-photo" role="img" aria-label="Team reviewing marketing charts on a laptop at a desk"></div>
  <p class="abs intro-wide">Did you know that more than 97% of all consumers turn to the internet to find both local as well as online solutions, whether they are searching for new furniture or legal representation? While traditional referrals and recommendations still go a long way for attorneys, providing online reviews and testimonials from previously satisfied clients can significantly boost your appeal and attractiveness to new prospective clients. With an online presence that truly showcases your skills, abilities, and experience. Tall Pine will outperform your local competition and help you solidify your place in the legal market as a professional, trustworthy, and authoritative business.</p>
  <div class="abs badges">
    <span class="badge-wide" role="img" aria-label="Partner certification badge"></span>
    <span class="badge-hex" role="img" aria-label="Certified planner badge"></span>
    <span class="badge-hex" role="img" aria-label="Certified buyer badge"></span>
    <span class="badge-wide alt" role="img" aria-label="Analytics certified partner badge"></span>
  </div>
</section>

<section class="why-band">
  <div class="abs why-box">
    <h2>Why you need an attorney marketing agency<br>specializing in the legal industry</h2>
    <p class="first">Not only do you need an omnichannel, cohesive law firm marketing strategy, but you also need a marketing company that understands the ins and outs of the legal industry, including regulations on advertising and marketing. We know:</p>
    <p>How to navigate the realm of legal disclosures, regulations, guidelines, and even marketing compliance requirements</p>
    <p>How the right legal marketing strategy can ultimately help you properly position your firm in your preferred market(s)</p>
    <p>How you can better navigate your long-term relationships with both prospective as well as loyal clients</p>
    <p>Working together with Tall Pine is one of the quickest ways to optimize your overall marketing and advertising budget while driving more referrals and leads directly to your online presence as well as your law firm itself. Learn more about how Tall Pine can help bring your digital marketing strategy and future campaigns to life below. Are you ready to get started with a brand new digital strategy that will help you attract new clients while generating leads? Contact us here to learn how we can help you and your legal presence with a winning digital marketing strategy today. Ready to begin? It all starts by contacting us here.</p>
  </div>
  <div class="abs dashboard" role="img" aria-label="Collage of marketing dashboard charts and reports"></div>
  <div class="abs services-copy">
    <h2 class="section-title">Lawyer Marketing Services<br><em>to Grow Your Practice</em></h2>
    <p>Wondering how to market your law firm? The best law firm marketing plans include a variety of online marketing strategies and services. Together, they work to increase brand authority, website traffic, leads, and new clients. See the services we recommend below, and we can’t wait to help your legal company grow!</p>
  </div>
  <a href="#" class="abs btn btn-red services-btn">LEARN MORE</a>
</section>

<section class="different">
  <h2 class="center-title">What makes Tall Pine <em>different</em></h2>
  <p class="abs different-lead" style="top:154px">At Tall Pine, we try and let our clients speak for us. Take a look at our attorney marketing reviews and hear straight from lawyers just like you why we are the best digital marketing company for your needs.</p>
  <p class="abs different-lead" style="top:204px">Done that? Great! Let’s get down to the details. Above all, everything we do comes from the perspective of a business owner, and we treat your business like our own. We can also offer you a few guarantees other companies can’t.</p>

  <div class="abs card" style="left:151px;top:297px">
    <svg viewBox="0 0 54 54" fill="none" stroke="#7d1414" stroke-width="2"><circle cx="27" cy="20" r="12"/><path d="M21 20l4 4 8-8M12 44l8-6h14l8 6"/></svg>
    <h4>You don’t have to worry about long-term contracts.</h4>
    <p>We won’t handcuff you for a specific amount of time. Ever.</p>
  </div>
  <div class="abs card" style="left:461px;top:297px">
    <svg viewBox="0 0 54 54" fill="none" stroke="#7d1414" stroke-width="2"><rect x="10" y="8" width="34" height="40" rx="2"/><path d="M16 18h22M16 26h22M16 34h14"/></svg>
    <h4>You’ll own every single deliverable, from your website to your content</h4>
    <p>Some digital marketing companies won’t let you keep your work when you leave. Not us.</p>
  </div>
  <div class="abs card" style="left:766px;top:297px">
    <svg viewBox="0 0 54 54" fill="none" stroke="#7d1414" stroke-width="2"><circle cx="27" cy="27" r="20"/><path d="M32 19h-7a4 4 0 000 8h4a4 4 0 010 8h-8M27 15v24"/></svg>
    <h4>You’ll optimize your marketing costs.</h4>
    <p>Everything we do is tracked, measured, and analyzed for improvements. This lowers your costs and increases results.</p>
  </div>
  <div class="abs card" style="left:151px;top:574px">
    <svg viewBox="0 0 54 54" fill="none" stroke="#7d1414" stroke-width="2"><path d="M8 38l10-8h10l6 4-8 2M8 38l8 8h14l16-12"/><circle cx="30" cy="16" r="8"/></svg>
    <h4>You get the peace of mind that we will bend over backward for you</h4>
    <p>Digital marketing is a long-term investment, which is why we believe in building partnerships, not acquiring clients.</p>
  </div>
  <div class="abs card" style="left:461px;top:574px">
    <svg viewBox="0 0 54 54" fill="none" stroke="#7d1414" stroke-width="2"><circle cx="27" cy="16" r="8"/><path d="M12 46c0-9 7-16 15-16s15 7 15 16z"/></svg>
    <h4>You get a dedicated account manager</h4>
    <p>to be your guide, as well as a support team that includes an analyst, web designer/developer, and a dedicated (US-based) copywriter.</p>
  </div>
  <div class="abs card" style="left:766px;top:574px">
    <svg viewBox="0 0 54 54" fill="none" stroke="#7d1414" stroke-width="2"><rect x="10" y="8" width="26" height="34"/><path d="M15 16h16M15 22h16M15 28h10"/><circle cx="38" cy="38" r="8"/><path d="M34 38l3 3 5-6"/></svg>
    <h4>You get detailed monthly reports</h4>
    <p>(you can actually understand) that connect campaign performance to your bottom line.</p>
  </div>
</section>

<section class="testimonials">
  <h2 class="center-title">What are industry leaders<br><em>saying about Tall Pine</em></h2>
  <svg class="abs arrow" style="left:140px" width="22" height="22" viewBox="0 0 22 22"><path d="M15 3L7 11l8 8" fill="none" stroke="#1c1c1c" stroke-width="3"/></svg>
  <div class="abs quote-card">
    <div class="abs quote-photo" role="img" aria-label="Portrait photo of Marcus Devlin"></div>
    <p class="abs quote-text">“Lorem ipsum dolor sit amet, consectetur adipiscing elit, sed do eiusmod tempor incididunt ut labore et dolore magna aliqua. Quis ipsum suspendisse ultrices gravida. Risus commodo viverra maecenas accumsan lacus vel facilisisidisse ultrices gravida. Risus commodo viverra maecenas accumsan lacus vel facilisis”</p>
    <p class="abs quote-name">MARCUS DEVLIN</p>
    <svg class="abs quote-mark" width="52" height="36" viewBox="0 0 52 36"><path d="M4 0h18v18l-8 18H6l6-18H4zM30 0h18v18l-8 18h-8l6-18h-8z" fill="#7d1414"/></svg>
  </div>
  <svg class="abs arrow" style="left:1014px" width="22" height="22" viewBox="0 0 22 22"><path d="M7 3l8 8-8 8" fill="none" stroke="#1c1c1c" stroke-width="3"/></svg>
</section>

<section class="featured">
  <h5>FEATURED IN</h5>
  <div class="abs press" style="left:130px" role="img" aria-label="Publication badge"><i></i></div>
  <div class="abs press" style="left:316px" role="img" aria-label="Publication badge"><i></i></div>
  <div class="abs press" style="left:509px" role="img" aria-label="Publication badge"><i></i></div>
  <div class="abs press" style="left:704px" role="img" aria-label="Publication badge"><i></i></div>
  <div class="abs press" style="left:900px" role="img" aria-label="Publication badge"><i></i></div>
</section>

<section class="office">
  <h2>Tall Pine Office</h2>
  <div class="abs contact-item" style="top:198px">
    <span class="contact-icon"><svg width="20" height="24" viewBox="0 0 20 24"><path d="M10 0a9 9 0 00-9 9c0 7 9 15 9 15s9-8 9-15a9 9 0 00-9-9z" fill="#7d1414"/><circle cx="10" cy="9" r="3.5" fill="#fff"/></svg></span>
    <span>Address: 418 W. Cedar Ave,<br>Suite 310, Mesa, 85201</span>
  </div>
  <div class="abs contact-item" style="top:266px">
    <span class="contact-icon"><svg width="20" height="20" viewBox="0 0 20 20"><path d="M4 1l4 4-2 3c1 3 3 5 6 6l3-2 4 4-3 3C8 19 1 12 1 4z" fill="#7d1414"/></svg></span>
    <span>(480) 555-0142</span>
  </div>
  <div class="abs contact-item" style="top:318px">
    <span class="contact-icon"><svg width="22" height="16" viewBox="0 0 22 16"><rect width="22" height="16" rx="2" fill="#7d1414"/><path d="M1 2l10 7 10-7" fill="none" stroke="#fff" stroke-width="1.6"/></svg></span>
    <span>sales@tallpine.agency</span>
  </div>
  <div class="abs office-photo" role="img" aria-label="Professional reviewing work on a tablet"></div>
</section>

<footer class="site-footer">
  <div class="brand abs footer-brand"><span class="brand-dot"></span><span class="brand-name">TALL PINE</span></div>
  <a href="#" class="abs btn btn-gray footer-call">CALL US (480) 555-0142</a>
  <a href="#" class="abs btn btn-red footer-grow">GROW YOUR REVENUE</a>
  <div class="abs footer-rule"></div>
  <div class="abs footer-col" style="left:147px">
    <h6>Quick Links</h6>
    <ul><li>About</li><li>Industries</li><li>Training</li><li>Blog</li><li>Services</li><li>Contact</li></ul>
  </div>
  <div class="abs footer-col" style="left:369px">
    <h6>Services</h6>
    <ul><li>Programmatic Advertising</li><li>Search Engine Marketing (SEM)</li><li>Search Engine Optimization (SEO)</li><li>Content Marketing</li><li>Email Marketing</li><li>Paid Search Advertising</li><li>Paid Social Advertising</li></ul>
  </div>
  <div class="abs footer-col" style="left:649px">
    <h6>Industries</h6>
    <ul><li>Ecommerce</li><li>Electricians</li><li>Financial Services Marketing</li><li>Home Builders</li><li>Home Services</li><li>Hvac Companies</li><li>Cosmetic Surgery Centers</li><li>Dental Marketing</li><li>Education</li><li>Healthcare Medical Marketing</li><li>Plumbing Companies</li><li>Podiatrist Marketing</li><li>Landscapers</li></ul>
  </div>
  <div class="abs footer-col" style="left:909px">
    <h6>Links</h6>
    <ul><li>Training</li><li>Resources</li><li>Privacy Policy</li><li>Sitemap</li><li>Terms Of Use</li><li>Press &amp; Media</li><li>Cookie Policy</li></ul>
  </div>
  <div class="abs copyright-rule"></div>
  <p class="abs copyright">© 2024 Company Name | All Rights Reserved</p>
</footer>

</body>
</html>
```